Local fast-growing company in the service sector

We are looking for a modern business card design, which should also appear on our letterheads

Target Market(s)

Private and industrial sectors

Contact Information for Business Card

Vorname Name
Kellberger Str. 18
73614 Lindenbrunn
Tel.: 07146-839214-0
Name@agentur-kvtl.de

Colors
9d9d9d
919191
aaaaaa

Requirements
Must have
• The logo (file) in silver

```html
<!DOCTYPE html>
<html lang="de">
<head>
<meta charset="utf-8">
<title>KVTL – Visitenkarte</title>
<link rel="stylesheet" href="https://fonts.googleapis.com/css2?family=Open+Sans:wght@400;600;700&display=swap">
<style>
  :root {
    --stage: #2b2c2f;
    --card-white: #f4f4f4;
    --silver-dark: #6f6f72;
    --silver-mid: #9d9d9d;
    --silver-light: #d6d6d8;
    --brand-grey: #919191;
    --text-dark: #3a3a3a;
    --text-body: #4a4a4a;
    --rule: #555555;
  }
  * { margin: 0; padding: 0; box-sizing: border-box; }
  html, body {
    width: 1200px; height: 864px; overflow: hidden;
    background: var(--stage);
    font-family: "Open Sans", Arial, sans-serif;
  }
  .sheet {
    position: relative; width: 1200px; height: 864px;
    display: flex; flex-direction: column; align-items: center; justify-content: center; gap: 44px;
  }
  .card {
    position: relative; width: 600px; height: 340px; border-radius: 4px;
    box-shadow: 0 10px 30px rgba(0,0,0,.45);
  }
  /* Back side */
  .card-back {
    background: linear-gradient(160deg, var(--silver-dark) 0%, var(--silver-mid) 35%, var(--silver-light) 52%, var(--silver-mid) 70%, var(--silver-dark) 100%);
    display: flex; align-items: center; justify-content: center; gap: 14px;
  }
  .card-back .brand-mark { width: 22px; height: 22px; background: #ffffff; }
  .card-back .brand-name {
    font-weight: 700; font-size: 64px; letter-spacing: 2px; color: #ffffff;
  }
  /* Front side */
  .card-front { background: var(--card-white); }
  .brand {
    position: absolute; right: 56px; top: 46px;
    display: flex; align-items: center; gap: 12px;
  }
  .brand .brand-mark { width: 34px; height: 34px; background: var(--brand-grey); }
  .brand-text { display: flex; flex-direction: column; line-height: 1; }
  .brand .brand-name { font-weight: 700; font-size: 44px; color: var(--brand-grey); letter-spacing: 1px; }
  .brand .brand-domain { font-weight: 700; font-size: 15px; color: var(--brand-grey); letter-spacing: .5px; margin-top: 2px; }
  .holder {
    position: absolute; left: 34px; top: 148px; right: 34px;
    display: flex; align-items: center; gap: 8px;
  }
  .holder-name { font-weight: 600; font-size: 17px; color: var(--text-dark); white-space: nowrap; }
  .holder-rule { flex: 1; height: 1.5px; background: var(--rule); margin-top: 6px; }
  .contacts {
    position: absolute; left: 36px; top: 186px; list-style: none;
    font-size: 13.5px; color: var(--text-body); line-height: 21px;
  }
  .contacts li { display: flex; align-items: center; gap: 8px; }
  .contacts svg { width: 11px; height: 11px; fill: var(--text-body); }
  .lower-rule {
    position: absolute; left: 232px; right: 34px; top: 222px; height: 1.5px; background: var(--rule);
  }
  .address {
    position: absolute; right: 40px; bottom: 28px; text-align: right;
    font-size: 14px; line-height: 21px; color: var(--text-body); font-style: normal;
  }
</style>
</head>
<body>
<main class="sheet">
  <section class="card card-back" aria-label="Kartenrückseite">
    <span class="brand-mark"></span>
    <span class="brand-name">KVTL</span>
  </section>

  <section class="card card-front" aria-label="Kartenvorderseite">
    <div class="brand">
      <span class="brand-mark"></span>
      <div class="brand-text">
        <span class="brand-name">KVTL</span>
        <span class="brand-domain">agentur-kvtl.de</span>
      </div>
    </div>

    <div class="holder">
      <span class="holder-name">VORNAME NAME</span>
      <span class="holder-rule"></span>
    </div>

    <ul class="contacts">
      <li>
        <svg viewBox="0 0 24 24" aria-hidden="true"><path d="M6.6 10.8a15.1 15.1 0 0 0 6.6 6.6l2.2-2.2c.3-.3.7-.4 1-.2 1.1.4 2.3.6 3.6.6.6 0 1 .4 1 1V20c0 .6-.4 1-1 1A17 17 0 0 1 3 4c0-.6.4-1 1-1h3.5c.6 0 1 .4 1 1 0 1.3.2 2.5.6 3.6.1.3 0 .7-.2 1z"/></svg>
        <span>07146-839214-0</span>
      </li>
      <li>
        <svg viewBox="0 0 24 24" aria-hidden="true"><path d="M2 5h20v14H2z M3 6l9 7 9-7" fill="none" stroke="#4a4a4a" stroke-width="2"/></svg>
        <span>Name@agentur-kvtl.de</span>
      </li>
      <li>
        <svg viewBox="0 0 24 24" aria-hidden="true"><circle cx="12" cy="12" r="10"/></svg>
        <span>www.agentur-kvtl.de</span>
      </li>
    </ul>

    <span class="lower-rule"></span>

    <address class="address">
      Kellberger Str. 18<br>
      73614 Lindenbrunn
    </address>
  </section>
</main>
</body>
</html>
```